Auntie Verdict Billboard

I need a billboard designed for a Personal Injury Law firm. I need to simple not busy. I am attaching the following as suggestions to use. Need good colors that show up from Road Simple that can leave people associating injury lawyer with Auntie Verdict. Big picture of Dottie. Need Auntieverdict.com and 555-417-9038 to be big. possiblly let the emojis do the talking for personal injury and money settlement. Colors for logo should be similar to website auntieverdict.com
Updates

Billboard size. 10.5ft. X 36ft.

Target Market(s)

Car Accident Victims

Font styles to use
Sans Serif

Requirements
Must have
• Picture of Dottie. auntieverdict.com. 555-417-9038. message needs to be clear that she is a personal injury attorney. Clear simple message. Colors bold and visable to highway drivers
Should not have
• Busy ad.

```html
<!DOCTYPE html>
<html lang="en">
<head>
<meta charset="utf-8">
<title>Auntie Verdict Billboard</title>
<link href="https://fonts.googleapis.com/css2?family=Open+Sans:wght@600;700;800&display=swap" rel="stylesheet">
<style>
  :root {
    --stage: #e6e7e9;
    --board: #f7f7f7;
    --navy-blue: #0a4f96;
    --brand-red: #c01f2f;
    --ink: #1b1f2a;
    --white: #ffffff;
    --photo-dark: #1c2230;
    --photo-light: #d9c3b5;
  }
  * { margin: 0; padding: 0; box-sizing: border-box; }
  html, body {
    width: 1200px;
    height: 960px;
    overflow: hidden;
    background: var(--stage);
    font-family: "Open Sans", Arial, sans-serif;
  }
  .billboard {
    position: absolute;
    left: 40px;
    top: 316px;
    width: 1120px;
    height: 328px;
    background: var(--board);
    box-shadow: 0 14px 30px rgba(0,0,0,0.18);
    overflow: hidden;
  }
  .attorney-portrait {
    position: absolute;
    left: 37px;
    top: 10px;
    width: 264px;
    height: 318px;
    border-radius: 110px 110px 0 0;
    background: linear-gradient(180deg, var(--photo-dark) 0%, var(--photo-light) 28%, var(--photo-dark) 55%, var(--photo-dark) 100%);
  }
  .firm-name {
    position: absolute;
    left: 326px;
    top: 58px;
    display: flex;
    align-items: center;
    gap: 10px;
    color: var(--ink);
    font-weight: 600;
    font-size: 34px;
    letter-spacing: 2px;
    line-height: 1;
  }
  .firm-name .mark {
    width: 22px;
    height: 22px;
    border-radius: 50%;
    background: var(--brand-red);
  }
  .firm-name .suffix {
    font-size: 9px;
    letter-spacing: 1px;
    align-self: flex-end;
    margin-bottom: 3px;
  }
  .web-pill {
    position: absolute;
    left: 707px;
    top: 35px;
    width: 358px;
    height: 40px;
    border-radius: 20px;
    background: var(--brand-red);
    color: var(--white);
    font-size: 13.5px;
    font-weight: 600;
    letter-spacing: 3px;
    display: flex;
    align-items: center;
    justify-content: center;
  }
  .web-pill strong { font-weight: 800; }
  .headline {
    position: absolute;
    left: 322px;
    top: 114px;
    color: var(--navy-blue);
    font-size: 90px;
    font-weight: 800;
    line-height: 1;
    letter-spacing: -1px;
    white-space: nowrap;
  }
  .call-pill {
    position: absolute;
    left: 319px;
    top: 223px;
    width: 756px;
    height: 81px;
    border-radius: 41px;
    background: var(--brand-red);
    color: var(--white);
    font-size: 66px;
    font-weight: 800;
    line-height: 1;
    display: flex;
    align-items: center;
    justify-content: center;
    letter-spacing: 0.5px;
  }
</style>
</head>
<body>
  <section class="billboard">
    <div class="attorney-portrait" role="img" aria-label="Portrait photo of the attorney in a dark suit"></div>
    <div class="firm-name"><span class="mark"></span>RK LAW FIRM<span class="suffix">PLLC</span></div>
    <div class="web-pill">WWW.<strong>AUNTIEVERDICT</strong>.COM</div>
    <h1 class="headline">AUNTIE VERDICT</h1>
    <div class="call-pill">CALL: 555-417-9038</div>
  </section>
</body>
</html>
```